Business card design for my company.
I would like the card's background colour to be black. You can also see our web site to get an idea of our brand. https://www.tmwhomecrafting.com.au/
- Name
- Email

```html
<!DOCTYPE html>
<html lang="en">
<head>
<meta charset="utf-8">
<title>TMW Home Crafting – Business Card</title>
<link rel="stylesheet" href="https://fonts.googleapis.com/css2?family=Montserrat:wght@400;600;700&display=swap">
<style>
  :root {
    --stage: #1c1c1c;
    --card: #141414;
    --green: #0e9748;
    --white: #f2f2f2;
    --text: #ffffff;
  }
  * { margin: 0; padding: 0; box-sizing: border-box; }
  html, body {
    width: 1200px; height: 1059px; overflow: hidden;
    background: var(--stage);
    font-family: "Montserrat", sans-serif;
  }
  .card {
    position: absolute;
    background: var(--card);
    border-radius: 20px;
    overflow: hidden;
    box-shadow: 0 12px 30px rgba(0,0,0,.55);
  }
  .card--front { left: 256px; top: 90px; width: 689px; height: 392px; }
  .card--back  { left: 253px; top: 545px; width: 694px; height: 397px; }

  .holder { position: absolute; left: 25px; top: 20px; }
  .holder__name {
    color: var(--green); font-weight: 700; font-size: 30px; line-height: 1.1;
  }
  .holder__role {
    color: var(--text); font-weight: 400; font-size: 17px; margin-top: 6px; letter-spacing: .3px;
  }
  .contact {
    position: absolute; left: 27px;
    display: flex; align-items: center; gap: 8px;
    color: var(--text); font-size: 17px; letter-spacing: .4px;
  }
  .contact svg { width: 15px; height: 15px; fill: var(--green); flex: none; }
  .contact--place { top: 155px; }
  .contact--phone { top: 250px; }
  .contact--mail  { top: 277px; }

  .wave { position: absolute; left: 0; top: 0; width: 100%; height: 100%; }
  .wave__green { fill: var(--green); }
  .wave__white { fill: var(--white); }

  .website {
    position: absolute; right: 27px; top: 343px;
    color: var(--text); font-size: 17px; letter-spacing: .3px;
  }

  .brand {
    position: absolute; text-align: center;
    color: var(--white); font-weight: 700; line-height: 1;
  }
  .brand__initials { display: block; letter-spacing: 4px; }
  .brand__words { display: block; letter-spacing: 6px; }
  .card--front .brand { left: 367px; width: 297px; top: 70px; }
  .card--front .brand__initials { font-size: 96px; }
  .card--front .brand__words { font-size: 18px; margin-top: 18px; }
  .card--back .brand { left: 0; width: 100%; top: 120px; }
  .card--back .brand__initials { font-size: 150px; }
  .card--back .brand__words { font-size: 27px; margin-top: 26px; letter-spacing: 9px; }
</style>
</head>
<body>
  <section class="card card--front">
    <svg class="wave" viewBox="0 0 689 392" preserveAspectRatio="none" aria-hidden="true">
      <path class="wave__white" d="M0,306 C90,340 200,347 300,336 C360,329 400,320 430,311 C380,321 330,336 260,346 C180,357 80,351 0,333 Z"/>
      <path class="wave__green" d="M0,344 C90,385 220,380 330,358 C480,328 580,292 689,292 V392 H0 Z"/>
    </svg>

    <div class="holder">
      <h1 class="holder__name">Dane Whitford</h1>
      <p class="holder__role">General Manager</p>
    </div>

    <p class="contact contact--place">
      <svg viewBox="0 0 24 24"><path d="M12 1a8 8 0 0 0-8 8c0 6 8 14 8 14s8-8 8-14a8 8 0 0 0-8-8zm0 11a3 3 0 1 1 0-6 3 3 0 0 1 0 6z"/></svg>
      Hobart, Tasmania, Australia
    </p>
    <p class="contact contact--phone">
      <svg viewBox="0 0 24 24"><path d="M2 9c0-3 4-5 10-5s10 2 10 5v2h-5V8c-3-1-7-1-10 0v3H2zM6 12h12l3 8H3z"/></svg>
      0400 555 184
    </p>
    <p class="contact contact--mail">
      <svg viewBox="0 0 24 24"><path d="M1 5h22v14H1z M1 5l11 8 11-8"/></svg>
      info@tmwhomecrafting.com.au
    </p>

    <div class="brand">
      <span class="brand__initials">TMW</span>
      <span class="brand__words">HOME CRAFTING</span>
    </div>

    <p class="website">www.tmwhomecrafting.com.au</p>
  </section>

  <section class="card card--back">
    <div class="brand">
      <span class="brand__initials">TMW</span>
      <span class="brand__words">HOME CRAFTING</span>
    </div>
  </section>
</body>
</html>
```